The Wardrobe Sage needs a pricing flyer

Single page flyer for The Wardrobe Sage.
The Wardrobe Sage is a lead generation service exclusively for the custom closet industry.
You design quality closets we provide quality leads!
Value Points:
Leads for closet companies are exclusive with a first right of refusal. Meaning, if the closet company cannot handle all of the leads we can provide, we will sell the excess to other closet companies. We will never sell the same lead to two different closet companies.
Benefits:
Flat rate and easy to budget
Cancel at anytime
Choose from 3 types of leads
Lower cost compared to overall cost per lead from other sources
More leads allows hiring more designers
More leads grow the companies revenue
Less time managing other advertising models
3 service options.
$250 each
- We send you the lead
- You and your team set the appointment
- Setting the appointment is up to you
2. $275 each
- We send you the lead
- We guarantee the appointment
- Return unset appointments for a replacement
3. $375 each
- We are your call center
- We generate the lead
- We set the appointment
Contact:
The Wardrobe Sage
704-555-0183
leads@TheWardrobeSage.com

```html
<!DOCTYPE html>
<html lang="en">
<head>
<meta charset="utf-8">
<title>The Wardrobe Sage – Pricing Flyer</title>
<link rel="stylesheet" href="https://fonts.googleapis.com/css2?family=Alegreya:wght@400;700&family=Pinyon+Script&family=Montserrat:wght@400;500;700&display=swap">
<style>
:root{
  --brown:#a8632c;
  --brown-dark:#8d4f20;
  --tan:#e6cdb4;
  --band:#4a4a4f;
  --ink:#2b2b2b;
  --muted:#555;
  --paper:#ffffff;
  --stage:#eef0f1;
}
*{box-sizing:border-box;margin:0;padding:0}
html,body{width:1200px;height:2282px;overflow:hidden;background:var(--stage)}
.stage{position:relative;width:1200px;height:2282px}
.flyer-wrap{position:absolute;left:50px;top:430px;width:1100px;height:1422px;box-shadow:0 10px 30px rgba(0,0,0,.18)}
.flyer{position:absolute;left:0;top:0;width:944px;height:1220px;background:var(--paper);transform:scale(1.1653);transform-origin:0 0;overflow:hidden;font-family:"Montserrat",sans-serif;color:var(--ink)}

.hero-photo{position:absolute;left:0;top:0;width:944px;height:545px;background:linear-gradient(100deg,#d9d6d2 0%,#ece9e5 35%,#cfc9c1 60%,#b9b1a6 100%)}
.hero-panel{position:absolute;left:28px;top:0;width:474px;height:460px;background:rgba(255,255,255,.62)}
.brand-top{position:absolute;left:28px;top:100px;width:474px;text-align:center;font-family:"Alegreya",serif;font-size:32px;color:var(--brown)}
.headline{position:absolute;left:28px;top:180px;width:474px;text-align:center;font-family:"Alegreya",serif;font-weight:700;color:var(--brown);line-height:1}
.headline .l1{font-size:52px;display:block}
.headline .l2{font-size:40px;display:block;margin-top:6px}
.headline .l3{font-family:"Pinyon Script",cursive;font-weight:400;font-size:40px;color:var(--muted);display:block;margin-top:6px}
.rule{position:absolute;left:245px;top:344px;width:40px;height:4px;background:var(--brown)}
.tagline{position:absolute;left:28px;top:360px;width:474px;text-align:center;font-family:"Alegreya",serif;font-weight:700;font-size:25px;line-height:34px;color:var(--muted)}

.value-band{position:absolute;left:0;top:513px;width:570px;height:118px;background:var(--band);padding:16px 10px 0 46px;color:#fff}
.value-band .lead{font-family:"Alegreya",serif;font-weight:700;font-size:15.5px;color:#e0924f;margin-bottom:3px}
.value-band p{font-size:13.2px;line-height:17px}

.inset-frame{position:absolute;left:570px;top:375px;width:336px;height:291px;background:var(--brown);border-radius:6px;padding:9px}
.inset-photo{width:100%;height:100%;border:2px solid #fff;background:radial-gradient(ellipse at 50% 60%,#e9dccd 0%,#7a5a44 45%,#3b2518 100%)}

.benefits-title{position:absolute;left:46px;top:645px;font-family:"Alegreya",serif;font-weight:700;font-size:30px;color:var(--brown)}
.benefits-box{position:absolute;left:160px;top:670px;width:231px;height:436px;border-top:1px solid var(--brown);border-right:1px solid var(--brown);border-bottom:1px solid var(--brown);border-radius:0 6px 6px 0}
.benefit{position:absolute;left:58px;width:312px;height:44px;display:flex;align-items:center;border-bottom:3px solid #eee}
.benefit .icon{width:40px;height:40px;border-radius:8px 8px 8px 2px;background:var(--brown);flex:none;display:flex;align-items:center;justify-content:center}
.benefit .text{margin-left:19px;font-size:14.6px;line-height:17px;color:var(--ink)}

.services-label{position:absolute;left:432px;top:1025px;transform:rotate(-90deg);transform-origin:0 0;font-family:"Alegreya",serif;font-weight:700;font-size:30px;letter-spacing:.5px;color:var(--brown);white-space:nowrap}
.services-line{position:absolute;left:430px;width:1px;background:var(--brown)}

.price{position:absolute;left:458px;width:114px;height:114px;border-radius:50%;background:var(--tan);padding:7px}
.price .disc{width:100%;height:100%;border-radius:50%;background:var(--brown);color:#fff;text-align:center;padding-top:14px}
.price .amt{font-family:"Alegreya",serif;font-size:38px;line-height:38px}
.price .amt sup{font-size:17px;vertical-align:14px}
.price .each{font-size:17px;letter-spacing:3px;line-height:20px}

.features{position:absolute;left:598px;width:300px;list-style:none}
.features li{position:relative;padding-left:23px;font-size:14.6px;line-height:17.5px;margin-bottom:7px;color:var(--ink)}
.features li svg{position:absolute;left:0;top:2px}
.divider{position:absolute;left:598px;width:300px;border-top:1px dashed #888}

.contact{position:absolute;left:450px;top:1112px;display:flex;gap:14px;font-size:17px;font-weight:500;color:var(--ink)}
.contact span{display:flex;align-items:center;gap:7px}
.web-bar{position:absolute;left:443px;top:1140px;width:501px;height:35px;background:var(--brown);color:#fff;display:flex;align-items:center;padding-left:12px;gap:8px;font-size:18px;letter-spacing:2.6px}
.web-bar b{font-weight:700}
.brand-foot{position:absolute;left:46px;top:1122px;font-family:"Alegreya",serif;font-size:42px;color:var(--muted)}
</style>
</head>
<body>
<div class="stage">
 <div class="flyer-wrap">
  <div class="flyer">
   <div class="hero-photo" role="img" aria-label="Bright white walk-in closet with shelving full of shoes and a chair by the window"></div>
   <div class="hero-panel"></div>
   <div class="brand-top">The Wardrobe Sage</div>
   <h1 class="headline">
     <span class="l1">A lead Generation</span>
     <span class="l2">Service Exclusively for</span>
     <span class="l3">The custom Closet Industry</span>
   </h1>
   <div class="rule"></div>
   <p class="tagline">You design quality closets<br>we provide quality leads!</p>

   <div class="value-band">
     <div class="lead">Leads for closet companies are exclusive with a first right of refusal.</div>
     <p>Meaning, if the closet company cannot handle all of the leads we can provide, we will sell the excess to other closet companies. We will never sell the same lead to two different closet companies.</p>
   </div>
   <div class="inset-frame"><div class="inset-photo" role="img" aria-label="Dark wood walk-in closet with a central island and a woman standing in it"></div></div>

   <h2 class="benefits-title">Benefits</h2>
   <div class="benefits-box"></div>
   <div class="benefit" style="top:698px"><div class="icon"><svg width="20" height="20" viewBox="0 0 20 20"><path d="M4 16L16 4M6 6h.1M14 14h.1" stroke="#fff" stroke-width="2" stroke-linecap="round"/></svg></div><div class="text">Flat rate and easy to budget</div></div>
   <div class="benefit" style="top:756px"><div class="icon"><svg width="20" height="20" viewBox="0 0 20 20"><circle cx="10" cy="10" r="7" fill="none" stroke="#fff" stroke-width="2"/><path d="M5 15L15 5" stroke="#fff" stroke-width="2"/></svg></div><div class="text">Cancel at anytime</div></div>
   <div class="benefit" style="top:818px"><div class="icon"><svg width="20" height="20" viewBox="0 0 20 20"><rect x="3" y="3" width="6" height="6" fill="none" stroke="#fff" stroke-width="1.6"/><rect x="11" y="3" width="6" height="6" fill="none" stroke="#fff" stroke-width="1.6"/><rect x="3" y="11" width="6" height="6" fill="none" stroke="#fff" stroke-width="1.6"/></svg></div><div class="text">Choose from 3 types of leads</div></div>
   <div class="benefit" style="top:872px;height:50px"><div class="icon"><svg width="20" height="20" viewBox="0 0 20 20"><circle cx="10" cy="10" r="7" fill="none" stroke="#fff" stroke-width="2"/><path d="M10 6v8" stroke="#fff" stroke-width="2"/></svg></div><div class="text">Lower cost compared to overall cost per lead from other sources</div></div>
   <div class="benefit" style="top:932px;height:50px"><div class="icon"><svg width="20" height="20" viewBox="0 0 20 20"><circle cx="10" cy="7" r="3" fill="#fff"/><path d="M4 17c0-4 12-4 12 0" fill="#fff"/></svg></div><div class="text">More leads allows hiring more designers</div></div>
   <div class="benefit" style="top:992px;height:50px"><div class="icon"><svg width="20" height="20" viewBox="0 0 20 20"><path d="M3 16l5-5 3 3 6-7" fill="none" stroke="#fff" stroke-width="2"/></svg></div><div class="text">More leads grow the companies revenue</div></div>
   <div class="benefit" style="top:1047px;height:50px;border-bottom:none"><div class="icon"><svg width="20" height="20" viewBox="0 0 20 20"><circle cx="10" cy="10" r="7" fill="none" stroke="#fff" stroke-width="2"/><path d="M10 6v4l3 2" fill="none" stroke="#fff" stroke-width="2"/></svg></div><div class="text">Less time managing other advertising models</div></div>

   <div class="services-line" style="top:688px;height:52px"></div>
   <div class="services-label">OUR 3 SERVICES</div>
   <div class="services-line" style="top:1030px;height:68px"></div>

   <div class="price" style="top:683px"><div class="disc"><div class="amt"><sup>$</sup>250</div><div class="each">EACH</div></div></div>
   <div class="price" style="top:827px"><div class="disc"><div class="amt"><sup>$</sup>275</div><div class="each">EACH</div></div></div>
   <div class="price" style="top:968px"><div class="disc"><div class="amt"><sup>$</sup>375</div><div class="each">EACH</div></div></div>

   <ul class="features" style="top:687px">
     <li><svg width="13" height="13" viewBox="0 0 13 13"><circle cx="6.5" cy="6.5" r="6.5" fill="var(--brown)"/><path d="M3.5 6.7l2 2 4-4.2" fill="none" stroke="#fff" stroke-width="1.6"/></svg>We send you the lead</li>
     <li><svg width="13" height="13" viewBox="0 0 13 13"><circle cx="6.5" cy="6.5" r="6.5" fill="var(--brown)"/><path d="M3.5 6.7l2 2 4-4.2" fill="none" stroke="#fff" stroke-width="1.6"/></svg>You and your team set the appointment</li>
     <li><svg width="13" height="13" viewBox="0 0 13 13"><circle cx="6.5" cy="6.5" r="6.5" fill="var(--brown)"/><path d="M3.5 6.7l2 2 4-4.2" fill="none" stroke="#fff" stroke-width="1.6"/></svg>Setting the appointment is up<br>to you</li>
   </ul>
   <div class="divider" style="top:807px"></div>
   <ul class="features" style="top:824px">
     <li><svg width="13" height="13" viewBox="0 0 13 13"><circle cx="6.5" cy="6.5" r="6.5" fill="var(--brown)"/><path d="M3.5 6.7l2 2 4-4.2" fill="none" stroke="#fff" stroke-width="1.6"/></svg>We send you the lead</li>
     <li><svg width="13" height="13" viewBox="0 0 13 13"><circle cx="6.5" cy="6.5" r="6.5" fill="var(--brown)"/><path d="M3.5 6.7l2 2 4-4.2" fill="none" stroke="#fff" stroke-width="1.6"/></svg>You and your team set the appointment</li>
     <li><svg width="13" height="13" viewBox="0 0 13 13"><circle cx="6.5" cy="6.5" r="6.5" fill="var(--brown)"/><path d="M3.5 6.7l2 2 4-4.2" fill="none" stroke="#fff" stroke-width="1.6"/></svg>We guarantee the appointment</li>
     <li><svg width="13" height="13" viewBox="0 0 13 13"><circle cx="6.5" cy="6.5" r="6.5" fill="var(--brown)"/><path d="M3.5 6.7l2 2 4-4.2" fill="none" stroke="#fff" stroke-width="1.6"/></svg>Return unset appointments for a replacement</li>
   </ul>
   <div class="divider" style="top:980px"></div>
   <ul class="features" style="top:1003px">
     <li><svg width="13" height="13" viewBox="0 0 13 13"><circle cx="6.5" cy="6.5" r="6.5" fill="var(--brown)"/><path d="M3.5 6.7l2 2 4-4.2" fill="none" stroke="#fff" stroke-width="1.6"/></svg>We are your call center</li>
     <li><svg width="13" height="13" viewBox="0 0 13 13"><circle cx="6.5" cy="6.5" r="6.5" fill="var(--brown)"/><path d="M3.5 6.7l2 2 4-4.2" fill="none" stroke="#fff" stroke-width="1.6"/></svg>We generate the lead</li>
     <li><svg width="13" height="13" viewBox="0 0 13 13"><circle cx="6.5" cy="6.5" r="6.5" fill="var(--brown)"/><path d="M3.5 6.7l2 2 4-4.2" fill="none" stroke="#fff" stroke-width="1.6"/></svg>We set the appointment</li>
   </ul>

   <div class="brand-foot">The Wardrobe Sage</div>
   <div class="contact">
     <span><svg width="16" height="16" viewBox="0 0 16 16"><circle cx="8" cy="8" r="8" fill="var(--brown)"/><path d="M5 4.5c0 4 2.5 6.5 6.5 6.5l.5-1.6-2-1-1 1c-1-.5-2-1.5-2.5-2.5l1-1-1-2z" fill="#fff"/></svg>704-555-0183</span>
     <span><svg width="16" height="16" viewBox="0 0 16 16"><circle cx="8" cy="8" r="8" fill="var(--brown)"/><rect x="4" y="5" width="8" height="6" fill="#fff"/><path d="M4 5l4 3 4-3" fill="none" stroke="var(--brown)" stroke-width="1"/></svg>leads@TheWardrobeSage.com</span>
   </div>
   <div class="web-bar"><svg width="15" height="15" viewBox="0 0 16 16"><circle cx="8" cy="8" r="6.5" fill="none" stroke="#fff" stroke-width="1.5"/><path d="M1.5 8h13M8 1.5c-3 3.5-3 9.5 0 13M8 1.5c3 3.5 3 9.5 0 13" fill="none" stroke="#fff" stroke-width="1.2"/></svg><span>www.<b>wardrobesagegreenville</b>.com</span></div>
  </div>
 </div>
</div>
</body>
</html>
```